Web Design for company in the healthcare industry

We need a web design for a new company in the healthcare industry (telehealth) which allows patients to schedule appointments at their convenience, view and monitor their results, and consult with specialists that fit their requirements. The aim is to help patients take charge of their own health.

We already have a logo (attached) and are working with a developer who will do all the back end programming once the design is ready. Apart from the colours in the logo, we think shades of gray would work well.

Target Market(s)

I imagine the vast majority would be professionals from 30-50 years old.

Industry/Entity Type

Health And Wellness

Number of Pages Required

4 page

Requirements
Must have
• Hand-sketched graphics, particularly on landing page.
Should not have
• We don't want any photographs of people

```html
<!DOCTYPE html>
<html lang="en">
<head>
<meta charset="utf-8">
<title>Medivane – Take Charge of Your Health</title>
<link rel="stylesheet" href="https://fonts.googleapis.com/css2?family=Open+Sans:wght@400;600;700&display=swap">
<style>
:root{
  --blue:#1d5fa8;
  --blue-dark:#174d8a;
  --footer:#1c5ba4;
  --footer-deep:#174c8a;
  --green:#8cc63f;
  --green-dark:#76ad2f;
  --ink:#3a3f45;
  --muted:#7d848b;
  --line:#d9dde1;
  --panel:#f2f3f5;
  --white:#ffffff;
}
*{box-sizing:border-box;margin:0;padding:0}
html,body{width:1200px;height:2272px;overflow:hidden}
body{font-family:"Open Sans",Arial,sans-serif;color:var(--ink);background:var(--white);position:relative}
.abs{position:absolute}

/* header */
.site-header{position:absolute;left:0;top:0;width:1200px;height:100px;background:var(--white);border-bottom:1px solid var(--line)}
.brand{position:absolute;left:100px;top:30px;display:flex;align-items:center;gap:10px}
.brand-dot{width:16px;height:16px;border-radius:50%;background:var(--green)}
.brand-name{font-size:40px;font-weight:600;color:var(--blue);letter-spacing:-0.5px;line-height:1}
.main-nav{position:absolute;right:100px;top:56px;display:flex;gap:38px;font-size:15px}
.main-nav a{color:var(--blue);text-decoration:none}
.main-nav a.active{color:var(--green);font-weight:600;border-bottom:2px solid var(--green);padding-bottom:4px}

/* headings */
.section-title{position:absolute;left:0;width:1200px;text-align:center;font-size:36px;font-weight:600;color:var(--blue);letter-spacing:0.5px}
.pulse{position:absolute;left:540px;width:120px;height:20px}

/* hero */
.hero{position:absolute;left:0;top:100px;width:1200px;height:670px;background:linear-gradient(180deg,#f5f6f7,#eceef0)}
.steps-line{position:absolute;left:0;top:0}
.step{position:absolute;width:240px;text-align:center}
.step-icon{width:112px;height:112px;border-radius:50%;background:var(--white);border:4px solid var(--green);margin:0 auto;display:flex;align-items:center;justify-content:center}
.step-label{margin-top:34px;font-size:17px;font-weight:600;color:var(--ink);line-height:1.3}
.step-text{margin:12px auto 0;width:190px;font-size:12px;color:var(--muted);line-height:1.6}
.btn-start{position:absolute;left:530px;top:562px;width:140px;height:36px;background:var(--green);color:var(--white);font-size:11px;font-weight:600;letter-spacing:0.5px;display:flex;align-items:center;justify-content:center;border-radius:2px}

/* packages */
.packages{position:absolute;left:0;top:770px;width:1200px;height:620px;background:var(--white)}
.carousel-arrow{position:absolute;top:380px;width:24px;height:40px}
.package-card{position:absolute;top:190px;width:300px;height:400px;background:var(--white);border:1px solid var(--line);padding:22px 24px}
.package-card.featured{box-shadow:0 6px 22px rgba(0,0,0,0.16);border-color:#e6e8ea}
.package-title{text-align:center;font-size:16px;color:var(--ink);height:24px}
.featured .package-title{color:var(--blue);font-weight:600}
.package-media{margin-top:14px;height:130px;border-radius:2px}
.package-text{margin-top:16px;text-align:center;font-size:12px;color:var(--muted);line-height:1.6;height:40px}
.price-row{margin-top:26px;display:flex;justify-content:space-between;font-size:12px}
.price-old{color:var(--muted);text-decoration:line-through}
.price-offer{margin-top:8px;text-align:center;font-size:15px;color:var(--green);font-weight:600}
.package-actions{margin-top:18px;display:flex;justify-content:flex-end;gap:8px}
.btn-small{width:80px;height:28px;font-size:10px;font-weight:600;color:var(--white);display:flex;align-items:center;justify-content:center;border-radius:2px;background:#5b6168}
.featured .btn-small{background:var(--blue)}

/* specialists */
.specialists{position:absolute;left:0;top:1390px;width:1200px;height:522px;background:var(--panel)}
.specialist-card{position:absolute;top:140px;width:245px;height:270px;background:var(--white);text-align:center;padding-top:24px}
.specialist-card.active{background:var(--green)}
.portrait{width:118px;height:118px;border-radius:50%;margin:0 auto;border:4px solid var(--white);box-shadow:0 0 0 1px var(--line)}
.specialist-name{margin-top:18px;font-size:16px;font-weight:700;color:var(--green);letter-spacing:0.5px}
.specialist-role{margin-top:4px;font-size:11px;color:var(--muted)}
.active .specialist-name,.active .specialist-role{color:var(--white)}
.btn-know{margin:16px auto 0;width:100px;height:28px;background:var(--green);color:var(--white);font-size:11px;font-weight:600;display:flex;align-items:center;justify-content:center;border-radius:2px}
.active .btn-know{background:var(--blue)}
.dots{position:absolute;left:0;width:1200px;display:flex;justify-content:center;gap:8px}
.dots span{width:10px;height:10px;border-radius:50%;border:1px solid var(--muted)}
.dots span.on{background:var(--blue);border-color:var(--blue)}

/* footer */
.site-footer{position:absolute;left:0;top:1912px;width:1200px;height:360px;background:var(--footer);color:var(--white)}
.footer-heading{font-size:14px;font-weight:600;letter-spacing:0.5px;text-transform:uppercase}
.quick-links{position:absolute;left:100px;top:44px}
.quick-links ul{list-style:none;margin-top:16px;font-size:12px;line-height:2}
.quick-links li::before{content:"› ";color:var(--green)}
.footer-map{position:absolute;left:340px;top:44px;width:180px;height:130px;border:3px solid var(--white)}
.get-in-touch{position:absolute;left:590px;top:44px;width:240px}
.get-in-touch p{margin-top:16px;font-size:12px;line-height:1.6;opacity:0.9}
.contact-list{list-style:none;margin-top:14px;font-size:12px;line-height:2}
.contact-list li{display:flex;align-items:center;gap:8px}
.contact-now{position:absolute;left:900px;top:44px;width:200px}
.contact-now p{margin-top:16px;font-size:12px;line-height:1.6;opacity:0.9}
.field{margin-top:10px;height:28px;background:var(--white);color:var(--muted);font-size:11px;padding:0 10px;display:flex;align-items:center}
.btn-submit{margin-top:10px;margin-left:auto;width:80px;height:28px;background:var(--green);font-size:11px;font-weight:600;display:flex;align-items:center;justify-content:center}
.social{margin-top:14px;display:flex;justify-content:flex-end;gap:10px}
.social span{width:16px;height:16px;border-radius:50%;background:var(--white);opacity:0.85}
.footer-bottom{position:absolute;left:0;top:300px;width:1200px;height:60px;border-top:1px solid rgba(255,255,255,0.25);padding:22px 100px;font-size:11px;opacity:0.85}
</style>
</head>
<body>

<header class="site-header">
  <div class="brand"><span class="brand-name">Medivane</span><span class="brand-dot"></span></div>
  <nav class="main-nav">
    <a class="active" href="#">Home</a>
    <a href="#">Health Packages</a>
    <a href="#">Appointment</a>
    <a href="#">Specialist</a>
    <a href="#">Contact Us</a>
  </nav>
</header>

<section class="hero">
  <h1 class="section-title" style="top:110px">TAKE CHARGE OF YOUR HEALTH</h1>
  <svg class="pulse" style="top:162px" viewBox="0 0 120 20"><polyline points="0,10 44,10 50,3 56,17 62,1 68,15 74,10 120,10" fill="none" stroke="#8cc63f" stroke-width="2"/></svg>

  <svg class="steps-line" width="1200" height="400" viewBox="0 0 1200 400">
    <g stroke="#8cc63f" stroke-width="2" fill="#8cc63f">
      <line x1="300" y1="316" x2="416" y2="316"/><polygon points="416,311 426,316 416,321" stroke="none"/>
      <line x1="540" y1="316" x2="656" y2="316"/><polygon points="656,311 666,316 656,321" stroke="none"/>
      <line x1="780" y1="316" x2="896" y2="316"/><polygon points="896,311 906,316 896,321" stroke="none"/>
    </g>
  </svg>

  <div class="step" style="left:120px;top:260px">
    <div class="step-icon"><svg width="50" height="50" viewBox="0 0 50 50" fill="none" stroke="#1d5fa8" stroke-width="2.5"><path d="M6 16 L25 6 L44 16 L44 36 L25 46 L6 36 Z"/><path d="M6 16 L25 26 L44 16 M25 26 L25 46"/></svg></div>
    <div class="step-label">Select a package</div>
    <p class="step-text">Browse our health packages and choose the one that fits your needs best.</p>
  </div>
  <div class="step" style="left:360px;top:260px">
    <div class="step-icon"><svg width="50" height="50" viewBox="0 0 50 50" fill="none" stroke="#1d5fa8" stroke-width="2.5"><rect x="6" y="10" width="38" height="34" rx="2"/><line x1="6" y1="20" x2="44" y2="20"/><line x1="15" y1="5" x2="15" y2="14"/><line x1="35" y1="5" x2="35" y2="14"/><path d="M17 32 L23 38 L34 27"/></svg></div>
    <div class="step-label">Schedule an appointment<br>at your convenience</div>
    <p class="step-text">Book a visit online at a time that suits your daily routine.</p>
  </div>
  <div class="step" style="left:600px;top:260px">
    <div class="step-icon"><svg width="50" height="50" viewBox="0 0 50 50" fill="none" stroke="#1d5fa8" stroke-width="2.5"><rect x="10" y="6" width="30" height="40" rx="2"/><line x1="17" y1="16" x2="33" y2="16"/><line x1="17" y1="24" x2="33" y2="24"/><path d="M17 36 L22 31 L27 35 L33 29"/></svg></div>
    <div class="step-label">Get your result back</div>
    <p class="step-text">View and track your lab results securely from any device you own.</p>
  </div>
  <div class="step" style="left:840px;top:260px">
    <div class="step-icon"><svg width="50" height="50" viewBox="0 0 50 50" fill="none" stroke="#1d5fa8" stroke-width="2.5"><path d="M25 42 C10 32 5 24 5 17 C5 10 10 6 16 6 C20 6 23 8 25 12 C27 8 30 6 34 6 C40 6 45 10 45 17 C45 24 40 32 25 42 Z"/><path d="M12 22 L19 22 L22 16 L27 28 L30 22 L38 22"/></svg></div>
    <div class="step-label">A healthier you</div>
    <p class="step-text">Follow expert advice and keep your wellbeing on track every day.</p>
  </div>

  <div class="btn-start">GET STARTED NOW</div>
</section>

<section class="packages">
  <h2 class="section-title" style="top:50px">HEALTH PACKAGES</h2>
  <svg class="pulse" style="top:102px" viewBox="0 0 120 20"><polyline points="0,10 44,10 50,3 56,17 62,1 68,15 74,10 120,10" fill="none" stroke="#8cc63f" stroke-width="2"/></svg>

  <svg class="carousel-arrow" style="left:52px" viewBox="0 0 24 40"><polyline points="18,4 6,20 18,36" fill="none" stroke="#9aa1a8" stroke-width="2"/></svg>
  <svg class="carousel-arrow" style="left:1124px" viewBox="0 0 24 40"><polyline points="6,4 18,20 6,36" fill="none" stroke="#9aa1a8" stroke-width="2"/></svg>

  <article class="package-card featured" style="left:120px">
    <h3 class="package-title">Woman Wellness Package</h3>
    <div class="package-media" role="img" aria-label="Sketch of a woman enjoying the outdoors" style="background:linear-gradient(135deg,#cfe3f4,#eef4f8 60%,#dbe7c9)"></div>
    <p class="package-text">Complete checkup covering key markers for a clear view of your health.</p>
    <div class="price-row"><span class="price-old">$299.00</span><span class="price-old">$9,999.00</span></div>
    <div class="price-offer">Offer Price: $299.00</div>
    <div class="package-actions"><span class="btn-small">BOOK NOW</span><span class="btn-small">KNOW MORE</span></div>
  </article>

  <article class="package-card" style="left:450px">
    <h3 class="package-title">Smart Heart Package</h3>
    <div class="package-media" role="img" aria-label="Illustration of a heart with a stethoscope" style="background:linear-gradient(135deg,#f1d9d9,#f7eeee 55%,#d7e6f2)"></div>
    <p class="package-text">Focused heart screening with ECG, lipid profile and expert cardiac review.</p>
    <div class="price-row"><span class="price-old">$299.00</span><span class="price-old">$9,999.00</span></div>
    <div class="price-offer">Offer Price: $543.00</div>
    <div class="package-actions"><span class="btn-small">BOOK NOW</span><span class="btn-small">KNOW MORE</span></div>
  </article>

  <article class="package-card" style="left:780px">
    <h3 class="package-title">Healthy @ 60 + MALES</h3>
    <div class="package-media" role="img" aria-label="Sketch of an older couple walking in a park" style="background:linear-gradient(135deg,#d6e8c2,#eef3e4 55%,#c9dcb0)"></div>
    <p class="package-text">Tailored screening for men over sixty with thorough age-specific tests.</p>
    <div class="price-row"><span class="price-old">$299.00</span><span class="price-old">$9,999.00</span></div>
    <div class="price-offer">Offer Price: $543.00</div>
    <div class="package-actions"><span class="btn-small">BOOK NOW</span><span class="btn-small">KNOW MORE</span></div>
  </article>
</section>

<section class="specialists">
  <h2 class="section-title" style="top:40px">OUR SPECIALISTS</h2>
  <svg class="pulse" style="top:92px" viewBox="0 0 120 20"><polyline points="0,10 44,10 50,3 56,17 62,1 68,15 74,10 120,10" fill="none" stroke="#8cc63f" stroke-width="2"/></svg>

  <article class="specialist-card active" style="left:90px">
    <div class="portrait" role="img" aria-label="Sketched portrait of the specialist" style="background:linear-gradient(160deg,#eef1f3,#cfd6dc)"></div>
    <h3 class="specialist-name">DR. NORA VALE</h3>
    <p class="specialist-role">Senior Cardio Specialist</p>
    <div class="btn-know">Know More</div>
  </article>
  <article class="specialist-card" style="left:355px">
    <div class="portrait" role="img" aria-label="Sketched portrait of the specialist" style="background:linear-gradient(160deg,#eef1f3,#cfd6dc)"></div>
    <h3 class="specialist-name">DR. OWEN MARSH</h3>
    <p class="specialist-role">Senior Cardio Specialist</p>
    <div class="btn-know">Know More</div>
  </article>
  <article class="specialist-card" style="left:620px">
    <div class="portrait" role="img" aria-label="Sketched portrait of the specialist" style="background:linear-gradient(160deg,#f1ece8,#d9cfc8)"></div>
    <h3 class="specialist-name">DR. LENA BROOKS</h3>
    <p class="specialist-role">Senior Cardio Specialist</p>
    <div class="btn-know">Know More</div>
  </article>
  <article class="specialist-card" style="left:885px">
    <div class="portrait" role="img" aria-label="Sketched portrait of the specialist" style="background:linear-gradient(160deg,#eef1f3,#cfd6dc)"></div>
    <h3 class="specialist-name">DR. ARLO QUINN</h3>
    <p class="specialist-role">Senior Cardio Specialist</p>
    <div class="btn-know">Know More</div>
  </article>

  <div class="dots" style="top:450px"><span></span><span class="on"></span><span></span></div>
</section>

<footer class="site-footer">
  <div class="quick-links">
    <h4 class="footer-heading">Quick Links</h4>
    <ul>
      <li>Home</li>
      <li>Health Packages</li>
      <li>Appointment</li>
      <li>Specialist</li>
      <li>Contact Us</li>
    </ul>
  </div>

  <div class="footer-map" role="img" aria-label="Map showing the clinic location" style="background:linear-gradient(135deg,#e6e9ec,#cdd3d8)"></div>

  <div class="get-in-touch">
    <h4 class="footer-heading">Get in Touch</h4>
    <p>Reach our care team any time for help with bookings and results.</p>
    <ul class="contact-list">
      <li><svg width="12" height="14" viewBox="0 0 12 14"><path d="M6 1 C3 1 1 3 1 6 C1 9 6 13 6 13 C6 13 11 9 11 6 C11 3 9 1 6 1 Z" fill="#8cc63f"/><circle cx="6" cy="6" r="2" fill="#1c5ba4"/></svg>48 Harbor Lane, Rivertown 20410</li>
      <li><svg width="12" height="14" viewBox="0 0 12 14"><path d="M2 1 L5 1 L6 4 L4 5 C5 8 6 9 8 10 L9 8 L12 9 L12 12 C6 12 1 7 1 2 Z" fill="#8cc63f"/></svg>+1 (555) 018 2044</li>
      <li><svg width="12" height="14" viewBox="0 0 12 14"><rect x="0.5" y="3" width="11" height="8" fill="none" stroke="#8cc63f"/><polyline points="0.5,3 6,8 11.5,3" fill="none" stroke="#8cc63f"/></svg>care@medivane.com</li>
    </ul>
  </div>

  <div class="contact-now">
    <h4 class="footer-heading">Contact Now</h4>
    <p>Leave your details and our team will call you back soon.</p>
    <div class="field">Email</div>
    <div class="field">Contact No</div>
    <div class="btn-submit">Submit</div>
    <div class="social"><span></span><span></span><span></span><span></span></div>
  </div>

  <div class="footer-bottom">© 2015 - Medivane. All Rights Reserved</div>
</footer>

</body>
</html>
```